Business Card for Vorla Parts Wholesale supplier

Hi There! I need a new business card for our company. We are specialized in selling Vorla parts, mostly we sell new LCD screens for Zelnar and Drelks. I would like to see that back in the design.

You can find the colors and logo's on our website: www.hartuvo.nl

Industry/Entity Type

Business

Contact Information for Business Card

My Details:
Tobias Lindqvist

Phone: 0031687203316
E-mail: Tobias@hartuvo.nl

Slogan: "Because Quality Matters"

Font styles to use
Sans Serif

Colors

Designer to choose colors to be used in the design.

Requirements
Must have
• A Black backside with the Hartuvo logo on it. The front side should be clean with only my contact details.
• But I'm also open for something really different or awesome!
Nice to have
• Remember that we are in the parts & repairing industry, So i'll be handing those business cards mainly to repair companies. Maybe you can do something with that thought :)

```html
<!DOCTYPE html>
<html lang="en">
<head>
<meta charset="UTF-8">
<title>Hartuvo Business Card</title>
<link rel="stylesheet" href="https://fonts.googleapis.com/css2?family=Open+Sans:wght@400;600;700;800&display=swap">
<style>
  :root {
    --stage: #2b2826;
    --card-black: #1b1b1c;
    --card-black-deep: #121213;
    --emboss: #3a3a3c;
    --orange: #f47521;
    --orange-deep: #e2611a;
    --white: #ffffff;
    --soft-white: #d9d9d9;
    --divider: #777777;
  }
  * { box-sizing: border-box; margin: 0; padding: 0; }
  html, body {
    width: 1200px;
    height: 715px;
    overflow: hidden;
    background: var(--stage);
    font-family: "Open Sans", Arial, sans-serif;
  }
  .canvas {
    position: relative;
    width: 1200px;
    height: 715px;
  }
  .card {
    position: absolute;
    top: 204px;
    width: 520px;
    height: 306px;
    border-radius: 6px;
    overflow: hidden;
    box-shadow: 0 10px 28px rgba(0,0,0,0.45);
  }
  /* Back side */
  .card-back {
    left: 60px;
    background: linear-gradient(135deg, var(--card-black) 0%, var(--card-black-deep) 100%);
    display: flex;
    align-items: center;
    justify-content: center;
  }
  .back-brand {
    display: flex;
    align-items: center;
    gap: 14px;
  }
  .back-brand .brand-dot {
    width: 38px;
    height: 38px;
    border-radius: 50%;
    background: var(--emboss);
  }
  .back-brand .brand-name {
    font-weight: 800;
    font-size: 46px;
    letter-spacing: 1px;
    color: var(--emboss);
  }
  /* Front side */
  .card-front {
    left: 620px;
    background: linear-gradient(160deg, #252526 0%, var(--card-black) 55%, var(--card-black-deep) 100%);
  }
  .front-brand {
    position: absolute;
    top: 26px;
    left: 30px;
    display: flex;
    align-items: center;
    gap: 12px;
  }
  .front-brand .brand-dot {
    width: 34px;
    height: 34px;
    border-radius: 50%;
    background: var(--orange);
  }
  .front-brand .brand-name {
    font-weight: 800;
    font-size: 40px;
    color: var(--white);
    letter-spacing: 0.5px;
  }
  .contact {
    position: absolute;
    top: 96px;
    left: 30px;
    color: var(--soft-white);
  }
  .person {
    display: flex;
    align-items: center;
    gap: 8px;
    margin-bottom: 8px;
  }
  .person-name {
    font-weight: 700;
    font-size: 15px;
    color: var(--white);
  }
  .person-divider {
    width: 1px;
    height: 14px;
    background: var(--divider);
  }
  .person-role {
    font-size: 11px;
    color: var(--soft-white);
  }
  .contact-line {
    display: flex;
    align-items: center;
    gap: 8px;
    font-size: 11.5px;
    line-height: 18px;
  }
  .contact-item {
    display: flex;
    align-items: center;
    gap: 6px;
  }
  .icon { width: 11px; height: 11px; flex: none; }
  .wave {
    position: absolute;
    left: 0;
    bottom: 0;
    width: 520px;
    height: 306px;
  }
  .slogan {
    position: absolute;
    right: 28px;
    bottom: 22px;
    text-align: right;
    color: var(--white);
    font-size: 14px;
    line-height: 18px;
  }
</style>
</head>
<body>
<main class="canvas">

  <section class="card card-back" aria-label="Card back">
    <div class="back-brand">
      <span class="brand-dot"></span>
      <span class="brand-name">hartuvo</span>
    </div>
  </section>

  <section class="card card-front" aria-label="Card front">
    <svg class="wave" viewBox="0 0 520 306" aria-hidden="true">
      <path d="M0,168 C130,182 260,228 520,206 L520,306 L0,306 Z" fill="var(--orange)"/>
      <path d="M0,178 C140,194 270,236 520,220 L520,226 C270,244 140,204 0,190 Z" fill="var(--card-black-deep)"/>
      <path d="M40,192 C170,214 290,246 520,236 L520,240 C290,252 170,222 40,196 Z" fill="var(--card-black-deep)"/>
      <path d="M0,260 C180,250 340,284 520,262 L520,306 L0,306 Z" fill="var(--orange-deep)" opacity="0.35"/>
    </svg>

    <div class="front-brand">
      <span class="brand-dot"></span>
      <span class="brand-name">hartuvo</span>
    </div>

    <div class="contact">
      <div class="person">
        <span class="person-name">Tobias Lindqvist</span>
        <span class="person-divider"></span>
        <span class="person-role">Managing Director</span>
      </div>
      <div class="contact-line">
        <span class="contact-item">
          <svg class="icon" viewBox="0 0 12 12" aria-hidden="true"><path d="M2.5 1 L4.5 1 L5.2 3.5 L4 4.5 C4.6 6 6 7.4 7.5 8 L8.5 6.8 L11 7.5 L11 9.5 C11 10.3 10.3 11 9.5 11 C5 11 1 7 1 2.5 C1 1.7 1.7 1 2.5 1 Z" fill="var(--orange)"/></svg>
          0031687203316
        </span>
      </div>
      <div class="contact-line">
        <span class="contact-item">
          <svg class="icon" viewBox="0 0 12 12" aria-hidden="true"><rect x="0.5" y="2" width="11" height="8" rx="1" fill="var(--orange)"/><path d="M1 2.6 L6 6.6 L11 2.6" stroke="var(--card-black)" stroke-width="1" fill="none"/></svg>
          Tobias@hartuvo.nl
        </span>
        <span class="contact-item">
          <svg class="icon" viewBox="0 0 12 12" aria-hidden="true"><circle cx="6" cy="6" r="5.3" fill="var(--orange)"/><ellipse cx="6" cy="6" rx="2.2" ry="5.3" stroke="var(--card-black)" stroke-width="0.8" fill="none"/><path d="M0.8 6 H11.2" stroke="var(--card-black)" stroke-width="0.8"/></svg>
          hartuvo.nl
        </span>
      </div>
    </div>

    <p class="slogan">Because<br>Quality Matters</p>
  </section>

</main>
</body>
</html>
```